World Wide News and Current Affairs website

We intends to start up a new website which deals on New and Current Affairs.
Attention Designers,
We want a home page design for this project. Our business is based in the United States. Our goal is to become a well known brand.
The website would consist of a category for News, Business and Tech.
The theme should be beautiful and attention seeking. The website would take bulk of it's news from the US, and Europe.
Designers can get inspiration from already existing new websites such as PWJ, KLV, DASKOLM.
All designs should be clean and easy to navigate.

```html
<!DOCTYPE html>
<html lang="en">
<head>
<meta charset="utf-8">
<title>Halvern News</title>
<link rel="stylesheet" href="https://fonts.googleapis.com/css2?family=Mulish:wght@400;600;700&display=swap">
<style>
:root{
  --ink:#1f1f1f;
  --muted:#666;
  --red:#c1111a;
  --red-deep:#b10d0f;
  --black:#000;
  --band-grey:#ebebeb;
  --dark:#2f2f30;
  --line:#dcdcdc;
  --white:#fff;
  --tag:#4a4a4a;
}
*{box-sizing:border-box;margin:0;padding:0}
html,body{width:1200px;height:3557px;overflow:hidden}
body{position:relative;background:var(--white);font-family:"Mulish",Arial,sans-serif;color:var(--ink)}
a{color:inherit;text-decoration:none}
.abs{position:absolute}
.photo{position:absolute;inset:0}

/* header */
.site-header{left:0;top:0;width:1200px;height:109px;background:var(--black)}
.brand{left:119px;top:36px;font-size:31px;font-weight:600;color:var(--white);letter-spacing:.2px;white-space:nowrap}
.main-nav{left:446px;top:42px;display:flex;align-items:center;font-size:16px;color:var(--white)}
.main-nav a{margin-right:34px}
.main-nav svg{display:block}

/* hero */
.hero{left:119px;top:138px;width:659px;height:424px;overflow:hidden}
.hero .photo{background:radial-gradient(circle at 28% 30%,#7fc4ee 0,#2b6fa6 22%,#0f2a4a 55%,#0a1320 100%)}
.hero-caption{position:absolute;left:39px;bottom:30px;color:var(--white)}
.hero-caption h2{font-size:28px;font-weight:600;margin-bottom:8px}
.hero-caption p{font-size:16px;font-weight:600}
.hero-arrows{position:absolute;right:22px;bottom:36px;display:flex;gap:20px}
.side-tile{left:790px;width:291px;height:204px;overflow:hidden;color:var(--white)}
.side-tile.top{top:138px}
.side-tile.top .photo{background:linear-gradient(135deg,#7a7572,#3b3735 60%,#5b4a44)}
.side-tile.market{top:358px;background:var(--red)}
.side-tile .label{position:absolute;left:19px;bottom:36px;font-size:22px;font-weight:600}
.side-tile .sub{position:absolute;left:19px;bottom:16px;font-size:13px}
.play-big{position:absolute;left:121px;top:60px}

/* section titles */
.section-title{font-size:25px;font-weight:400;letter-spacing:.5px;color:var(--ink)}

/* cards */
.card{position:absolute;background:var(--white)}
.card .media{position:relative;overflow:hidden}
.tag{position:absolute;left:0;bottom:0;background:var(--tag);color:var(--white);font-size:13px;padding:4px 14px}
.card h3{font-size:17px;font-weight:700;margin:0 0 10px}
.card p{font-size:13.5px;line-height:20px;color:var(--muted)}
.read-more{display:block;font-size:13px;font-weight:600;color:var(--red);text-transform:uppercase;margin-top:18px}

.latest .card{top:652px;width:311px;height:347px;box-shadow:0 0 0 1px var(--line),0 2px 4px rgba(0,0,0,.12)}
.latest .media{height:190px}
.latest .body{padding:16px 22px}

/* feature block */
.feature{left:123px;top:1046px;width:631px;height:344px;overflow:hidden}
.feature .photo{background:linear-gradient(160deg,#cfcfcc,#8d8b86 45%,#4a4845)}
.feature-caption{position:absolute;left:0;right:0;bottom:0;padding:14px 28px 16px;background:linear-gradient(transparent,rgba(0,0,0,.65));color:var(--white)}
.feature-caption h3{font-size:21px;font-weight:600;margin-bottom:4px}
.feature-caption p{font-size:13px}
.news-list{left:774px;top:1048px;width:307px}
.news-item{display:flex;height:112px;margin-bottom:10px;border-bottom:1px solid var(--line)}
.news-item:last-child{border-bottom:none}
.news-item .thumb{width:119px;height:99px;flex:none;margin-right:15px}
.news-item h4{font-size:14px;font-weight:600;margin:2px 0 6px}
.news-item p{font-size:12.5px;line-height:18px;color:var(--muted)}
.news-item a{display:block;font-size:12.5px;font-weight:700;color:var(--red);margin-top:8px}

/* current affairs */
.affairs .card{top:1501px;width:474px}
.affairs .media{height:223px}
.affairs .body{padding:22px 4px 0}
.affairs h3{font-size:18px}

/* grey band */
.grey-band{left:0;top:1905px;width:1200px;height:425px;background:var(--band-grey)}
.quad .card{top:1945px;width:231px;background:transparent}
.quad .media{height:161px}
.quad .body{padding:20px 4px 0}
.quad h3{font-size:16px;font-weight:600}
.quad .read-more{margin-top:14px}

/* videos */
.video-band{left:0;top:2332px;width:1200px;height:379px;background:var(--red-deep)}
.video-band .section-title{position:absolute;left:0;right:0;top:39px;text-align:center;color:var(--white);font-weight:600}
.video{position:absolute;top:2427px;width:311px}
.video .media{position:relative;height:182px;overflow:hidden}
.video .play{position:absolute;left:50%;top:50%;transform:translate(-50%,-50%)}
.video p{font-size:14px;line-height:20px;color:#f2b9b9;margin-top:10px;max-width:270px}

/* top featured */
.dark-band{left:0;top:2711px;width:1200px;height:439px;background:radial-gradient(circle at 70% 20%,#4a4a4b,#2c2c2d 55%,#1e1e1f)}
.dark-band .section-title{position:absolute;left:116px;top:46px;color:var(--white);font-size:30px}
.top-card{position:absolute;top:2806px;height:282px;overflow:hidden;color:var(--white)}
.top-card .caption{position:absolute;left:26px;bottom:22px}
.top-card h3{font-size:20px;font-weight:600;margin-bottom:4px}
.top-card p{font-size:13.5px}

/* footer */
.footer-cols{left:130px;top:3210px;display:flex}
.footer-col h5{font-size:20px;font-weight:400;letter-spacing:.5px;margin-bottom:24px}
.footer-col li{list-style:none;font-size:14px;line-height:26px;color:#333}
.social{display:flex;gap:6px}
.social span{width:31px;height:31px;border:2px solid var(--red);border-radius:50%;display:block}
.copyright{left:0;top:3482px;width:1200px;height:75px;background:#e3e3e3;text-align:center;font-size:13px;color:#777;line-height:75px}
</style>
</head>
<body>

<header class="site-header abs">
  <div class="brand abs">Halvern News</div>
  <nav class="main-nav abs">
    <a href="#" aria-label="Home"><svg width="22" height="18" viewBox="0 0 22 18"><path d="M11 1 1 9.5h3V17h5v-5h4v5h5V9.5h3z" fill="#fff"/></svg></a>
    <a href="#">News</a><a href="#">Featured</a><a href="#">Business</a><a href="#">Tech</a><a href="#">Blogs</a><a href="#">More</a>
    <a href="#" aria-label="Search"><svg width="18" height="18" viewBox="0 0 18 18"><circle cx="10" cy="7" r="5" fill="none" stroke="#fff" stroke-width="2"/><path d="M6.5 10.5 2 15" stroke="#fff" stroke-width="2"/></svg></a>
  </nav>
</header>

<section class="hero abs">
  <div class="photo" role="img" aria-label="Hand touching a glowing digital globe"></div>
  <div class="hero-caption">
    <h2>Porttitor mattis enim massa libero</h2>
    <p>interdum nec interdum vel blandit sed nulla In ullamcorper est</p>
  </div>
  <div class="hero-arrows">
    <svg width="12" height="20" viewBox="0 0 12 20"><path d="M10 2 2 10l8 8" fill="none" stroke="#fff" stroke-width="2.5"/></svg>
    <svg width="12" height="20" viewBox="0 0 12 20"><path d="M2 2l8 8-8 8" fill="none" stroke="#fff" stroke-width="2.5"/></svg>
  </div>
</section>
<div class="side-tile top abs">
  <div class="photo" role="img" aria-label="People working at a laptop"></div>
  <div class="label">TODAY'S TOP</div>
  <div class="sub">porttitor mattis enim in massa libero</div>
</div>
<div class="side-tile market abs">
  <svg class="play-big" width="50" height="50" viewBox="0 0 50 50"><circle cx="25" cy="25" r="23" fill="none" stroke="#fff" stroke-width="2.5"/><circle cx="25" cy="25" r="17" fill="#fff"/><path d="M21 17v16l12-8z" fill="#c1111a"/></svg>
  <div class="label">THE MARKET</div>
  <div class="sub">porttitor mattis enim in massa libero</div>
</div>

<h2 class="section-title abs" style="left:117px;top:600px">LATEST NEWS</h2>
<section class="latest">
  <article class="card" style="left:119px">
    <div class="media"><div class="photo" role="img" aria-label="Team laughing in a meeting" style="background:linear-gradient(135deg,#e6dccb,#b59d7e 50%,#6f5b47)"></div><span class="tag">Business</span></div>
    <div class="body"><h3>Class aptent taciti soci</h3><p>conubia nostra per inceptos hymenaeos Proin nulla arcu nonummy luctus dictum eget fermentum et lorem</p><a class="read-more" href="#">Read more</a></div>
  </article>
  <article class="card" style="left:444px">
    <div class="media"><div class="photo" role="img" aria-label="Hands reviewing finance charts on a tablet" style="background:linear-gradient(135deg,#eef2f6,#b7c8da 50%,#6e8aa8)"></div><span class="tag">Finance</span></div>
    <div class="body"><h3>Class aptent taciti soci</h3><p>conubia nostra per inceptos hymenaeos Proin nulla arcu nonummy luctus dictum eget fermentum et lorem</p><a class="read-more" href="#">Read more</a></div>
  </article>
  <article class="card" style="left:770px">
    <div class="media"><div class="photo" role="img" aria-label="Technician working at a bench" style="background:linear-gradient(135deg,#8e6d52,#4a3628 55%,#2a1e17)"></div><span class="tag">Tech</span></div>
    <div class="body"><h3>Class aptent taciti soci</h3><p>conubia nostra per inceptos hymenaeos Proin nulla arcu nonummy luctus dictum eget fermentum et lorem</p><a class="read-more" href="#">Read more</a></div>
  </article>
</section>

<section class="feature abs">
  <div class="photo" role="img" aria-label="Overhead view of a team around a desk with laptops"></div>
  <div class="feature-caption"><h3>Donec scelerisque leo ac risus</h3><p>aciisis volutpat in imperdiet sit amet sem Aliquam nec erat et purus cursus interdum</p></div>
</section>
<div class="news-list abs">
  <div class="news-item"><div class="thumb" role="img" aria-label="Blue circuit technology" style="background:linear-gradient(135deg,#0c1f3a,#1f5a8f,#0a1628)"></div><div><h4>News Tittle here</h4><p>ummy luctus dictum eget fermentum et lorem</p><a href="#">Read More</a></div></div>
  <div class="news-item"><div class="thumb" role="img" aria-label="Blue digital wave" style="background:linear-gradient(135deg,#123a66,#2f7bbf,#0e2848)"></div><div><h4>News Tittle here</h4><p>ummy luctus dictum eget fermentum et lorem</p><a href="#">Read More</a></div></div>
  <div class="news-item"><div class="thumb" role="img" aria-label="Person at a workshop" style="background:linear-gradient(135deg,#8a7563,#3d302a,#6a5246)"></div><div><h4>News Tittle here</h4><p>ummy luctus dictum eget fermentum et lorem</p><a href="#">Read More</a></div></div>
</div>

<h2 class="section-title abs" style="left:121px;top:1452px">CURRENT AFFAIRS</h2>
<section class="affairs">
  <article class="card" style="left:121px">
    <div class="media"><div class="photo" role="img" aria-label="Hands typing on a laptop with light effects" style="background:linear-gradient(135deg,#dfe9f3,#7fa3c6 50%,#2f5680)"></div><span class="tag">Business</span></div>
    <div class="body"><h3>Morbi diam mauris viverra in gravida</h3><p>conubia nostra per inceptos hymenaeos Proin nulla arcu nonummy luctus dictum eget fermentum et lorem</p><a class="read-more" href="#">Read more</a></div>
  </article>
  <article class="card" style="left:609px">
    <div class="media"><div class="photo" role="img" aria-label="Hands touching a digital technology interface" style="background:linear-gradient(135deg,#1b4a82,#3a86c8 50%,#0d2546)"></div><span class="tag">Business</span></div>
    <div class="body"><h3>Quisque dignissim congue leo</h3><p>conubia nostra per inceptos hymenaeos Proin nulla arcu nonummy luctus dictum eget fermentum et lorem</p><a class="read-more" href="#">Read more</a></div>
  </article>
</section>

<div class="grey-band abs"></div>
<section class="quad">
  <article class="card" style="left:119px">
    <div class="media"><div class="photo" role="img" aria-label="Speaker at a press event" style="background:linear-gradient(135deg,#3b3a3e,#6b6a70,#222)"></div><span class="tag">Tech</span></div>
    <div class="body"><h3>Tittle goes here</h3><p>conubia nostra per inceptos hymenaeos Proin nulla arcu nonummy luctus dictum eget fermentum et lorem</p><a class="read-more" href="#">Read more</a></div>
  </article>
  <article class="card" style="left:363px">
    <div class="media"><div class="photo" role="img" aria-label="Circuit board close-up" style="background:linear-gradient(135deg,#3f8f5a,#1e5a38,#8fbf9a)"></div><span class="tag">Tech</span></div>
    <div class="body"><h3>Tittle goes here</h3><p>conubia nostra per inceptos hymenaeos Proin nulla arcu nonummy luctus dictum eget fermentum et lorem</p><a class="read-more" href="#">Read more</a></div>
  </article>
  <article class="card" style="left:609px">
    <div class="media"><div class="photo" role="img" aria-label="Hands working on a laptop" style="background:linear-gradient(135deg,#e8d2b5,#b08a62,#6b4d33)"></div><span class="tag">Business</span></div>
    <div class="body"><h3>Tittle goes here</h3><p>conubia nostra per inceptos hymenaeos Proin nulla arcu nonummy luctus dictum eget fermentum et lorem</p><a class="read-more" href="#">Read more</a></div>
  </article>
  <article class="card" style="left:851px">
    <div class="media"><div class="photo" role="img" aria-label="Hands on a digital screen" style="background:linear-gradient(135deg,#e9e6e4,#c6b3a6,#8c7565)"></div><span class="tag">Tech</span></div>
    <div class="body"><h3>Tittle goes here</h3><p>conubia nostra per inceptos hymenaeos Proin nulla arcu nonummy luctus dictum eget fermentum et lorem</p><a class="read-more" href="#">Read more</a></div>
  </article>
</section>

<section class="video-band abs"><h2 class="section-title">WATCH VIDEOS</h2></section>
<article class="video" style="left:116px">
  <div class="media"><div class="photo" role="img" aria-label="Panel of people at a conference" style="background:linear-gradient(135deg,#2d2a35,#5b5262,#1b1920)"></div>
  <svg class="play" width="46" height="46" viewBox="0 0 46 46"><circle cx="23" cy="23" r="21" fill="#111" stroke="#fff" stroke-width="3"/><path d="M18 14v18l14-9z" fill="#fff"/></svg></div>
  <p>Morbi diam mauris viverra in gravida eu mattis in ante Morbi eget</p>
</article>
<article class="video" style="left:441px">
  <div class="media"><div class="photo" role="img" aria-label="Crowd at a street demonstration" style="background:linear-gradient(135deg,#3a3a3a,#7a7a7a,#1c1c1c)"></div>
  <svg class="play" width="46" height="46" viewBox="0 0 46 46"><circle cx="23" cy="23" r="21" fill="#111" stroke="#fff" stroke-width="3"/><path d="M18 14v18l14-9z" fill="#fff"/></svg></div>
  <p style="max-width:220px">Donec dictum lectus non odio Cras a ante vitae</p>
</article>
<article class="video" style="left:770px">
  <div class="media"><div class="photo" role="img" aria-label="Business handshake" style="background:linear-gradient(135deg,#5a88b8,#c9d6e3,#2d4f78)"></div>
  <svg class="play" width="46" height="46" viewBox="0 0 46 46"><circle cx="23" cy="23" r="21" fill="#111" stroke="#fff" stroke-width="3"/><path d="M18 14v18l14-9z" fill="#fff"/></svg></div>
  <p>Etiam eu urna Sed porta Suspendisse quam leo molestie</p>
</article>

<section class="dark-band abs"><h2 class="section-title">Top Featured</h2></section>
<article class="top-card" style="left:116px;width:467px">
  <div class="photo" role="img" aria-label="Politician shaking hands with a crowd" style="background:linear-gradient(135deg,#6f8ea4,#3a5466 50%,#1d2a33)"></div>
  <div class="caption"><h3>Class aptent taciti</h3><p>Aonubia nostra per inceptos hymenaeos Proin</p></div>
</article>
<article class="top-card" style="left:609px;width:472px">
  <div class="photo" role="img" aria-label="Official speaking at a press conference" style="background:linear-gradient(135deg,#6d4b43,#3e2a26 55%,#1e1513)"></div>
  <div class="caption"><h3>Morbi diam mauris viverra in gravida</h3><p>Aonubia nostra per inceptos hymenaeos</p></div>
</article>

<footer class="footer-cols abs">
  <div class="footer-col" style="width:214px"><h5>QUICK LINKS</h5><ul><li>Home</li><li>About Us</li><li>Videos</li><li>Top News</li><li>Current Affairs</li><li>Blogs</li></ul></div>
  <div class="footer-col" style="width:221px"><h5>FEATURES</h5><ul><li>Class aptent</li><li>Taciti sociosqu</li><li>Ad litora</li><li>Porquent</li><li>Ler conubia</li><li>Bostra per inceptos</li></ul></div>
  <div class="footer-col" style="width:227px"><h5>RESOURCES</h5><ul><li>Support</li><li>TV Shows</li><li>Finance</li><li>Business</li><li>Advertise</li></ul></div>
  <div class="footer-col"><h5>SOCIAL</h5><div class="social" aria-label="Social links"><span></span><span></span><span></span><span></span><span></span><span></span></div></div>
</footer>

<div class="copyright abs">© 2017 Company Name &nbsp;All right reserved &nbsp;Term of Use</div>

</body>
</html>
```